Need a vitamin/supplement label

Hi,
I need a vitamin label designing for a product that will be sold online.
The label needs to have the following information on the front:
1) B12
2) Methycobalamin
3) 1000mcg
4) 90 Lozenges
5) Sublingual
6) Dietary Supplement
7) Vegetarian
Numbers 1 and 2 need to standout the most because the product will only be sold online so visibility is key.
Use this design as an inspiration:
http://www.shopvelmara.com/Corvelle-Naturals-Methylcobalamin-5000mcg-Lozenges/dp/Q7742KXRTA/ref=sr_1_2?ie=UTF8&qid=1381433791&sr=8-2&keywords=b12
The label should come across as premium.
The brand name is 'Quarlen Nutra' and I haven't had a logo designed so there's some freedom when it comes to that. It needs to be simple and clean.
If you need any clarifications then let me know.
Online

```html
<!DOCTYPE html>
<html lang="en">
<head>
<meta charset="utf-8">
<title>Quarlen Nutra B-12 Label</title>
<link rel="stylesheet" href="https://fonts.googleapis.com/css2?family=Arimo:ital,wght@0,400;0,700;1,700&family=Tinos:wght@400&display=swap">
<style>
  :root {
    --bg: #e9e9e9;
    --label: #ffffff;
    --red: #d9413f;
    --red-deep: #a8191c;
    --red-text: #b3262a;
    --brand: #7a4a48;
    --ink: #3d3d3d;
    --rule: #c23a3a;
  }
  * { margin: 0; padding: 0; box-sizing: border-box; }
  html, body { width: 1200px; height: 960px; overflow: hidden; background: var(--bg); }
  .canvas { position: relative; width: 1200px; height: 960px; }
  .label {
    position: absolute; left: 150px; top: 100px; width: 900px; height: 760px;
    background: var(--label); overflow: hidden;
    box-shadow: 0 6px 24px rgba(0,0,0,0.12);
  }
  .top-accent {
    position: absolute; left: 0; top: 70px; width: 110px; height: 38px; background: var(--red);
  }
  .brand {
    position: absolute; left: 150px; top: 58px; display: flex; align-items: center; gap: 12px;
  }
  .brand-mark { width: 22px; height: 22px; background: var(--red-deep); }
  .brand-name {
    font-family: "Tinos", serif; font-size: 48px; font-weight: 400; color: var(--brand);
  }
  .visual-brain {
    position: absolute; left: 640px; top: 20px; width: 230px; height: 230px; border-radius: 50%;
    background: radial-gradient(circle, #d9646a 0%, #b8424a 30%, #8f9486 55%, rgba(255,255,255,0) 72%);
  }
  .tagline {
    position: absolute; left: 110px; top: 140px; width: 520px; text-align: right;
    font-family: "Arimo", sans-serif; font-style: italic; font-weight: 700;
    font-size: 30px; line-height: 40px; color: var(--red-text);
  }
  .name-band {
    position: absolute; left: 0; top: 250px; width: 800px; height: 210px;
    background: linear-gradient(90deg, #d63a3a 0%, #e25b5b 60%, #e56464 100%);
    clip-path: polygon(0 0, 740px 0, 800px 60px, 800px 100%, 0 100%);
  }
  .product-name {
    position: absolute; left: 0; top: 250px; width: 800px; text-align: center;
    font-family: "Arimo", sans-serif; font-weight: 700; font-size: 190px; line-height: 170px;
    color: #ffffff; letter-spacing: 4px;
  }
  .ingredient-band {
    position: absolute; left: 220px; top: 420px; width: 580px; height: 52px;
    background: linear-gradient(90deg, rgba(168,25,28,0) 0%, var(--red-deep) 25%, var(--red-deep) 100%);
    border-radius: 0 0 26px 0;
  }
  .ingredient {
    position: absolute; left: 220px; top: 420px; width: 580px; text-align: center;
    font-family: "Arimo", sans-serif; font-weight: 700; font-size: 34px; line-height: 52px;
    color: #ffffff; letter-spacing: 4px; text-transform: uppercase;
  }
  .features { position: absolute; left: 300px; top: 505px; list-style: none; }
  .features li {
    font-family: "Arimo", sans-serif; font-weight: 700; font-size: 34px; line-height: 46px;
    color: var(--ink); display: flex; align-items: center; gap: 12px;
  }
  .features li::before { content: ""; width: 9px; height: 9px; background: var(--red); }
  .features li:nth-child(2) { margin-left: 22px; }
  .features li:nth-child(3) { margin-left: 44px; }
  .rule { position: absolute; left: 200px; top: 665px; width: 500px; height: 2px; background: var(--rule); }
  .dosage {
    position: absolute; left: 200px; top: 680px; width: 500px; text-align: center;
    font-family: "Arimo", sans-serif; font-weight: 700; font-size: 28px; color: var(--ink);
    word-spacing: 4px;
  }
</style>
</head>
<body>
<div class="canvas">
  <div class="label">
    <div class="top-accent"></div>
    <div class="brand">
      <span class="brand-mark"></span>
      <span class="brand-name">Quarlen Nutra</span>
    </div>
    <div class="visual-brain" role="img" aria-label="Illustration of a glowing red brain"></div>
    <p class="tagline">Supports Nerve Cells and<br>Brain Tissue</p>
    <div class="name-band"></div>
    <h1 class="product-name">B-12</h1>
    <div class="ingredient-band"></div>
    <p class="ingredient">Methycobalamin</p>
    <ul class="features">
      <li>Sublingual</li>
      <li>Dietary Supplement</li>
      <li>Vegetarian</li>
    </ul>
    <div class="rule"></div>
    <p class="dosage">1000mcg &nbsp;I&nbsp; 90 Lozenges</p>
  </div>
</div>
</body>
</html>
```